Animal Horse & Bedding Company Needs a Website Coded & Designed

We need a website for a new animal bedding and feed company that is visually grabbing and vibrant. We would like to see a website that displays trust, quality and confidence. Needs to be responsive and mobile friendly for all browsers and coded for both Android & IOS. SEO is also important.

Joomla or Wordpress – must be both desktop and mobile friendly with fast page load speed. Need the ability to edit ourselves in Wordpress or Joomla.

Full details attached below with some layout and content ideas.

Coding

Coded - Design and coding required

Number of Pages Required

5+ page

Font styles to use
Sans Serif

Requirements
Must have
• Needs to be responsive and mobile friendly for all browsers and coded for both Android & IOS. SEO is also important.

Wordpress – must be both desktop and mobile friendly with fast page load speed. Need the ability to edit ourselves in Wordpress.

Logo Colours:
Dark Brown
CMYK: 50 / 70 / 80 / 70
Pantone: 4625C

Orange
CMYK: 0 / 50 / 100 / 0
Pantone: 144C
Nice to have
• Use picture of building attached and super impose logo on building.

```html
<!DOCTYPE html>
<html lang="en">
<head>
<meta charset="utf-8">
<title>Golden Bale – Bedding &amp; Feed</title>
<link rel="stylesheet" href="https://fonts.googleapis.com/css2?family=Bebas+Neue&family=Montserrat:wght@700;800&family=Open+Sans:wght@400;600;700&display=swap">
<style>
:root{
  --brown:#4a2511;
  --brown-dark:#3d2113;
  --orange:#f7941d;
  --orange-deep:#ef7f0f;
  --text:#4b4b4b;
  --light:#f6f6f7;
  --white:#ffffff;
}
*{box-sizing:border-box;margin:0;padding:0}
html,body{width:1200px;height:3619px;overflow:hidden}
body{position:relative;background:var(--white);font-family:"Open Sans",sans-serif;color:var(--text)}
.abs{position:absolute}

/* header */
.topbar{left:632px;top:0;width:568px;height:40px;background:var(--brown);border-bottom-left-radius:0;clip-path:polygon(28px 0,100% 0,100% 100%,0 100%)}
.topbar-item{top:9px;display:flex;align-items:center;gap:10px;color:var(--white);font-size:14px}
.topbar-item .dot{width:24px;height:24px;border-radius:50%;background:var(--orange);display:flex;align-items:center;justify-content:center}
.header-line{left:0;top:2px;width:632px;height:1px;background:var(--brown)}
.brand{display:flex;align-items:center;gap:12px;font-family:"Bebas Neue",sans-serif;color:var(--brown);letter-spacing:3px}
.brand .mark{border-radius:50%;border:3px solid var(--orange)}
.site-brand{left:162px;top:30px;font-size:42px}
.site-brand .mark{width:50px;height:50px}
.nav{top:70px;font-size:14px;font-weight:600;color:var(--brown)}
.nav.active{color:var(--orange)}
.btn{display:flex;align-items:center;justify-content:center;background:var(--orange);color:var(--white);border-radius:20px;font-size:14px;font-weight:600}
.btn-quote{left:906px;top:60px;width:131px;height:38px;box-shadow:0 0 0 2px var(--white),0 0 0 3px var(--orange)}

/* hero */
.hero{left:0;top:119px;width:1200px;height:548px;background:linear-gradient(180deg,#3d5a22 0%,#5b7a2d 35%,#8c9a45 55%,#7d7b3c 80%,#5a4f2a 100%)}
.hero-title{left:0;top:555px;width:1200px;text-align:center;font-family:"Montserrat",sans-serif;font-weight:800;font-size:37px;color:var(--white);letter-spacing:-.5px}

/* about */
.about{left:0;top:667px;width:1200px;height:900px;background:var(--light)}
.notch{left:560px;top:660px}
.about-head{left:0;top:750px;width:1200px;display:flex;justify-content:center;align-items:center;gap:16px;font-family:"Bebas Neue",sans-serif;font-size:46px;letter-spacing:2px}
.about-head .tag{color:var(--orange)}
.about-head .brand{font-size:40px}
.about-head .mark{width:42px;height:42px}
.lead{left:210px;top:830px;width:780px;text-align:center;font-weight:700;font-size:15px;line-height:24px;color:var(--brown)}
.copy{left:220px;top:916px;width:760px;text-align:center;font-size:15px;line-height:27px;color:var(--text)}

.feature-circle{width:162px;height:162px;border-radius:50%;background:var(--light);box-shadow:0 6px 18px rgba(0,0,0,.07);display:flex;align-items:center;justify-content:center}
.feature-title{width:300px;text-align:center;font-family:"Bebas Neue",sans-serif;font-size:22px;letter-spacing:.5px;color:var(--brown)}
.feature-text{width:300px;text-align:center;font-size:15px;line-height:24px;color:var(--text)}

/* section headings */
.section-head{font-family:"Bebas Neue",sans-serif;font-size:42px;letter-spacing:1.5px;color:var(--brown)}
.section-head .accent{color:var(--orange)}
.photo{border-radius:12px}
.checklist{list-style:none;font-size:15px;color:var(--brown)}
.checklist li{display:flex;align-items:flex-start;gap:12px;height:34px}
.checklist svg{flex:none;margin-top:4px}
.btn-more{width:121px;height:32px;font-size:13px;box-shadow:0 0 0 1px var(--brown-dark)}

/* delivery */
.flags{left:285px;top:2934px;width:180px;height:80px;background:linear-gradient(90deg,#2c4a8a 0%,#b8364a 38%,#e8e8ea 55%,#d9232c 70%,#f2f2f2 85%,#d9232c 100%);clip-path:polygon(0 18%,100% 0,100% 82%,0 100%)}
.delivery{left:485px;top:2938px;font-family:"Bebas Neue",sans-serif;font-size:50px;letter-spacing:1px;color:var(--brown)}

/* newsletter */
.newsletter{left:0;top:3045px;width:1200px;height:285px;background:var(--light)}
.news-title{left:200px;top:3128px;width:240px;text-align:right;font-family:"Bebas Neue",sans-serif;font-size:42px;line-height:44px;color:var(--brown-dark)}
.news-divider{left:468px;top:3098px;width:2px;height:183px;background:#dcdcdc}
.news-caption{left:513px;top:3148px;font-size:13px;color:#777}
.news-form{left:506px;top:3178px;width:482px;height:40px;border:1px solid #d8d8d8;border-radius:20px;background:var(--white);display:flex;align-items:center;justify-content:space-between;padding:0 3px 0 18px;font-size:13px;color:var(--text)}
.news-form .btn{width:117px;height:32px;font-size:13px}

/* footer */
.footer{left:0;top:3330px;width:1200px;height:289px;background:var(--brown-dark)}
.footer-brand{left:160px;top:3435px;width:260px;justify-content:center;color:var(--white);font-size:42px;flex-direction:column;gap:10px}
.footer-brand .mark{width:56px;height:56px}
.contact-icon{width:60px;height:60px;border-radius:50%;background:var(--orange);display:flex;align-items:center;justify-content:center}
.contact-label{width:220px;text-align:center;color:var(--white);font-size:13px;line-height:17px}
.contact-value{font-size:20px}
.copyright{left:163px;top:3575px;font-size:12px;font-weight:600;color:var(--white)}
.copyright u{text-decoration:underline}
.social{top:3574px;width:22px;height:22px;border-radius:50%}
</style>
</head>
<body>

<!-- Header -->
<div class="abs header-line"></div>
<div class="abs topbar"></div>
<div class="abs topbar-item" style="left:680px">
  <span class="dot"><svg width="12" height="12" viewBox="0 0 12 12"><path d="M1 6 11 1 8 11 6 7z" fill="#fff"/></svg></span>inquiry@goldenbale.com
</div>
<div class="abs topbar-item" style="left:910px">
  <span class="dot"><svg width="12" height="12" viewBox="0 0 24 24"><path d="M6 2l4 5-2 3a12 12 0 006 6l3-2 5 4-2 4C10 22 2 14 2 4z" fill="#fff"/></svg></span>555 014 2290
</div>

<div class="abs brand site-brand"><span class="mark"></span>GOLDEN BALE</div>

<div class="abs nav active" style="left:526px">Home</div>
<div class="abs nav" style="left:598px">About</div>
<div class="abs nav" style="left:670px">Feed</div>
<div class="abs nav" style="left:735px">Bedding</div>
<div class="abs nav" style="left:825px">Contact</div>
<div class="abs btn btn-quote">Request Quote</div>

<!-- Hero -->
<div class="abs hero" role="img" aria-label="Horses grazing in a green pasture in front of a forest"></div>
<h1 class="abs hero-title">WE ARE ANIMAL BEDDING AND FEED COMPANY</h1>

<!-- About -->
<div class="abs about"></div>
<svg class="abs notch" width="80" height="36" viewBox="0 0 80 36">
  <path d="M0 7 C20 7 26 34 40 34 C54 34 60 7 80 7 L80 36 L0 36z" fill="#f6f6f7"/>
  <path d="M0 7 C20 7 26 34 40 34 C54 34 60 7 80 7 L80 0 L0 0z" fill="#6b6135"/>
  <rect x="31" y="2" width="18" height="25" rx="9" fill="none" stroke="#f7941d" stroke-width="2"/>
  <path d="M36 12l4 4 4-4M36 17l4 4 4-4" fill="none" stroke="#f7941d" stroke-width="1.6"/>
</svg>

<div class="abs about-head"><span class="tag">ABOUT</span><span class="brand"><span class="mark"></span>GOLDEN BALE</span></div>
<p class="abs lead">Looking for the best bedding and feed for your horse, livestock or household pet look no further.&nbsp; We use premium locally sourced straw and hay in all of our products and are committed in providing quality products and service.</p>
<p class="abs copy">Your animal deserves the very best in health and comfort to keep them healthy, strong and happy.&nbsp; Our products are designed for horses, livestock (goats, cattle and sheep), small caged animals (rabbits, guinea pigs and more). Golden Bale offers supply and delivery of fresh bedding as well as removal of waste bedding.&nbsp; Let us deliver you a container of fresh straw and haul your waste bedding away.&nbsp; A full service solution that is sustainable and responsible.</p>

<svg class="abs" style="left:0;top:1160px" width="1200" height="150" viewBox="0 0 1200 150">
  <path d="M0 80 C80 120 160 140 225 125 M388 100 C430 80 480 60 520 50 M680 50 C720 60 770 80 812 110 M973 125 C1060 110 1140 80 1200 20" fill="none" stroke="#e6dcc4" stroke-width="1.5" stroke-dasharray="5 5"/>
</svg>

<div class="abs feature-circle" style="left:519px;top:1089px">
  <svg width="72" height="72" viewBox="0 0 72 72" fill="none" stroke-width="2.5" stroke-linecap="round" stroke-linejoin="round">
    <circle cx="36" cy="20" r="11" stroke="#f7941d"/><path d="M36 26V15m-4 4 4-4 4 4" stroke="#f7941d"/>
    <path d="M8 30c0 10 4 18 12 24v8h10v-8c-2-6-6-8-10-14M64 30c0 10-4 18-12 24v8H42v-8c2-6 6-8 10-14" stroke="#4a2511"/>
  </svg>
</div>
<div class="abs feature-title" style="left:450px;top:1270px">FULL SERVICE SOLUTION</div>
<div class="abs feature-text" style="left:450px;top:1300px">Dedicated in providing a full<br>service solution of bedding<br>supply &amp; waste removal</div>

<div class="abs feature-circle" style="left:225px;top:1192px">
  <svg width="66" height="80" viewBox="0 0 66 80" fill="none" stroke-width="2.5" stroke-linejoin="round">
    <path d="M33 4l7 6 9-1 2 9 8 5-4 8 4 8-8 5-2 9-9-1-7 6-7-6-9 1-2-9-8-5 4-8-4-8 8-5 2-9 9 1z" stroke="#4a2511"/>
    <circle cx="33" cy="32" r="12" stroke="#f7941d"/>
    <path d="M20 56 10 74l8-2 4 7 8-17M46 56l10 18-8-2-4 7-8-17" stroke="#4a2511"/>
    <text x="33" y="38" text-anchor="middle" font-size="16" font-family="Open Sans,sans-serif" fill="#f7941d" stroke="none">$</text>
  </svg>
</div>
<div class="abs feature-title" style="left:156px;top:1374px">QUALITY GUARANTEED</div>
<div class="abs feature-text" style="left:156px;top:1404px">Grown for quality - 100% natural<br>with no chemicals or additives</div>

<div class="abs feature-circle" style="left:811px;top:1192px">
  <svg width="86" height="72" viewBox="0 0 86 72" fill="none" stroke-width="2.5" stroke-linejoin="round" stroke-linecap="round">
    <circle cx="48" cy="16" r="12" stroke="#f7941d"/>
    <text x="48" y="22" text-anchor="middle" font-size="16" font-family="Open Sans,sans-serif" fill="#f7941d" stroke="none">$</text>
    <path d="M4 58l14-14c6-4 12-4 18 0h14c4 0 4 6 0 6H36M50 48l18-10c6-2 8 4 4 8L52 60c-6 4-14 4-22 2l-12 2" stroke="#4a2511"/>
    <circle cx="14" cy="60" r="2" fill="#4a2511" stroke="none"/>
  </svg>
</div>
<div class="abs feature-title" style="left:742px;top:1375px">CONVENIENT &amp; COST EFFECTIVE</div>
<div class="abs feature-text" style="left:742px;top:1405px">Compressed bags , pellets or bulk<br>products saving in shipping costs</div>

<!-- Bedding benefits -->
<div class="abs photo" style="left:162px;top:1696px;width:418px;height:385px;background:linear-gradient(135deg,#3a2416 0%,#7a4a2a 35%,#d8d2c8 55%,#8a5532 75%,#4a3420 100%)" role="img" aria-label="Two horses grazing on straw bedding"></div>
<h2 class="abs section-head" style="left:621px;top:1690px"><span class="accent">BEDDING</span> BENEFITS</h2>
<div class="abs" style="left:621px;top:1752px;width:53px;height:3px;background:var(--brown)"></div>
<ul class="abs checklist" style="left:621px;top:1781px;width:360px">
  <li><svg width="18" height="12" viewBox="0 0 18 12"><path d="M1 6l3 3 6-7M7 8l2 2 7-8" fill="none" stroke="#f7941d" stroke-width="1.5"/></svg>100% Natural Chopped Straw</li>
  <li><svg width="18" height="12" viewBox="0 0 18 12"><path d="M1 6l3 3 6-7M7 8l2 2 7-8" fill="none" stroke="#f7941d" stroke-width="1.5"/></svg>Low Dust</li>
  <li><svg width="18" height="12" viewBox="0 0 18 12"><path d="M1 6l3 3 6-7M7 8l2 2 7-8" fill="none" stroke="#f7941d" stroke-width="1.5"/></svg>Chemical &amp; Additive Free</li>
  <li><svg width="18" height="12" viewBox="0 0 18 12"><path d="M1 6l3 3 6-7M7 8l2 2 7-8" fill="none" stroke="#f7941d" stroke-width="1.5"/></svg>Clean &amp; Highly Absorbent</li>
  <li><svg width="18" height="12" viewBox="0 0 18 12"><path d="M1 6l3 3 6-7M7 8l2 2 7-8" fill="none" stroke="#f7941d" stroke-width="1.5"/></svg>Cheaper than Wood Shavings</li>
  <li><svg width="18" height="12" viewBox="0 0 18 12"><path d="M1 6l3 3 6-7M7 8l2 2 7-8" fill="none" stroke="#f7941d" stroke-width="1.5"/></svg>Economic – less used and less wasted</li>
  <li style="height:auto;line-height:24px"><svg width="18" height="12" viewBox="0 0 18 12"><path d="M1 6l3 3 6-7M7 8l2 2 7-8" fill="none" stroke="#f7941d" stroke-width="1.5"/></svg>Environmentally Friendly – Recyclable &amp;<br>Compostable</li>
</ul>
<div class="abs btn btn-more" style="left:621px;top:2050px">KNOW MORE</div>

<!-- Feed benefits -->
<h2 class="abs section-head" style="left:0;top:2184px;width:1200px;text-align:center"><span class="accent">FEED</span> BENEFITS</h2>
<p class="abs" style="left:190px;top:2268px;width:820px;text-align:center;font-size:15px;line-height:24px">Hay cubes and pellets are made from premium hay offering a variety of animals a feed that is non-GMO and packed with natural nutrients.&nbsp; These pellets and cubes are less bulky to handle, store and ship. As well, they reduce the amount of wasted feed.</p>
<ul class="abs checklist" style="left:162px;top:2403px;width:420px;line-height:0">
  <li style="height:35.3px;line-height:22px"><svg width="18" height="12" viewBox="0 0 18 12"><path d="M1 6l3 3 6-7M7 8l2 2 7-8" fill="none" stroke="#f7941d" stroke-width="1.5"/></svg>100% Natural</li>
  <li style="height:35.3px;line-height:22px"><svg width="18" height="12" viewBox="0 0 18 12"><path d="M1 6l3 3 6-7M7 8l2 2 7-8" fill="none" stroke="#f7941d" stroke-width="1.5"/></svg>Chemical &amp; Additive Free</li>
  <li style="height:35.3px;line-height:22px"><svg width="18" height="12" viewBox="0 0 18 12"><path d="M1 6l3 3 6-7M7 8l2 2 7-8" fill="none" stroke="#f7941d" stroke-width="1.5"/></svg>Available in Pellets or Cubes</li>
  <li style="height:35.3px;line-height:22px"><svg width="18" height="12" viewBox="0 0 18 12"><path d="M1 6l3 3 6-7M7 8l2 2 7-8" fill="none" stroke="#f7941d" stroke-width="1.5"/></svg>High Protein Content</li>
  <li style="height:35.3px;line-height:22px"><svg width="18" height="12" viewBox="0 0 18 12"><path d="M1 6l3 3 6-7M7 8l2 2 7-8" fill="none" stroke="#f7941d" stroke-width="1.5"/></svg>Eliminate Waste In Feeding</li>
  <li style="height:35.3px;line-height:22px"><svg width="18" height="12" viewBox="0 0 18 12"><path d="M1 6l3 3 6-7M7 8l2 2 7-8" fill="none" stroke="#f7941d" stroke-width="1.5"/></svg>Clean - Eliminates Dust From Feeding Baled Hay</li>
  <li style="height:35.3px;line-height:22px"><svg width="18" height="12" viewBox="0 0 18 12"><path d="M1 6l3 3 6-7M7 8l2 2 7-8" fill="none" stroke="#f7941d" stroke-width="1.5"/></svg>Cost Effective</li>
  <li style="height:35.3px;line-height:22px"><svg width="18" height="12" viewBox="0 0 18 12"><path d="M1 6l3 3 6-7M7 8l2 2 7-8" fill="none" stroke="#f7941d" stroke-width="1.5"/></svg>Convenient</li>
  <li style="height:35.3px;line-height:22px"><svg width="18" height="12" viewBox="0 0 18 12"><path d="M1 6l3 3 6-7M7 8l2 2 7-8" fill="none" stroke="#f7941d" stroke-width="1.5"/></svg>Less wasted feed</li>
</ul>
<div class="abs btn btn-more" style="left:162px;top:2726px">KNOW MORE</div>
<div class="abs photo" style="left:620px;top:2380px;width:418px;height:387px;background:linear-gradient(135deg,#2d3a28 0%,#b8642e 30%,#d89a6a 55%,#e8c9a8 70%,#6a5a30 100%)" role="img" aria-label="Chestnut horses eating hay in a stable"></div>

<!-- Delivery -->
<div class="abs flags" role="img" aria-label="United States and Canada flags"></div>
<div class="abs delivery">DELIVERY IN USA &amp; CANADA</div>

<!-- Newsletter -->
<div class="abs newsletter"></div>
<div class="abs news-title">NEWSLETTER<br>SIGN UP</div>
<div class="abs news-divider"></div>
<div class="abs news-caption">Subscribe to our newsletter to get the latest update to your inbox</div>
<div class="abs news-form"><span>Enter your email address</span><span class="btn">SUBSCRIBE</span></div>

<!-- Footer -->
<div class="abs footer"></div>
<div class="abs brand footer-brand" style="display:flex"><span class="mark"></span>GOLDEN BALE</div>

<div class="abs contact-icon" style="left:518px;top:3391px">
  <svg width="22" height="28" viewBox="0 0 22 28"><path d="M11 1a10 10 0 00-10 10c0 7 10 16 10 16s10-9 10-16A10 10 0 0011 1z" fill="#fff"/><circle cx="11" cy="11" r="4" fill="#f7941d"/></svg>
</div>
<div class="abs contact-label" style="left:438px;top:3476px">Delivery in Canada<br>&amp; USA</div>

<div class="abs contact-icon" style="left:715px;top:3391px">
  <svg width="26" height="26" viewBox="0 0 24 24"><path d="M6 2l4 5-2 3a12 12 0 006 6l3-2 5 4-2 4C10 22 2 14 2 4z" fill="#fff"/></svg>
</div>
<div class="abs contact-label" style="left:635px;top:3467px">PHONE<br><span class="contact-value">555 014 2290</span></div>

<div class="abs contact-icon" style="left:931px;top:3391px">
  <svg width="26" height="20" viewBox="0 0 26 20"><rect x="1" y="1" width="24" height="18" rx="2" fill="#fff"/><path d="M2 3l11 8 11-8" fill="none" stroke="#f7941d" stroke-width="2"/></svg>
</div>
<div class="abs contact-label" style="left:851px;top:3467px">EMAIL<br><span style="font-size:15px;line-height:26px">info@goldenbale.com</span></div>

<div class="abs copyright">Copyright 2021 Golden Bale Animal Feed.All Rights Reserved | <u>SITE MAP</u></div>
<span class="abs social" style="left:917px;background:#3b5998"></span>
<span class="abs social" style="left:950px;background:#1da1f2"></span>
<span class="abs social" style="left:983px;background:#0077b5"></span>
<span class="abs social" style="left:1016px;background:#6b7a8f"></span>

</body>
</html>
```